Business card for Sports Apparel business

DOUBLE SIDED DESIGN
We need business cards for a new sports apparel business. We are developing a protective headband for soccer initially.
Torvalle is focused on designing and developing head protection products to reduce the likelihood of concussion when playing sports. Exploring and understanding medical insights, material science research, current and former players experiences and governing bodies guidelines has allowed Torvalle to develop the safety, style, form and function requirements of a suitable product to bring to market.
Target Market(s)
Mums buying kits for the sons and daughters. Amateur footballers.
Industry/Entity Type
Sporting Good
Contact Information for Business Card
Martin Ashworth - CEO
Mobile: +44 7431589027
Email: martin@torvalle.co.uk
Tel: 0208 5519372
Helena Pargeter - COO
Mob: +44 7385 640117
Email: helena@torvalle.co.uk
Tel: 0208 5519372
Duncan Farrow - CCO
Mob: +44 7564 293081
Email: duncan@torvalle.co.uk
Tel: 0208 5519372
Look and feel
Each slider illustrates characteristics of the customer's brand and the style your logo design should communicate.

```html
<!DOCTYPE html>
<html lang="en">
<head>
<meta charset="utf-8">
<title>Torvalle Business Card</title>
<link href="https://fonts.googleapis.com/css2?family=Open+Sans:wght@400;600;700&display=swap" rel="stylesheet">
<style>
  :root {
    --bg: #d7d7d7;
    --brand-blue: #1467aa;
    --brand-blue-dark: #0f5a98;
    --brand-blue-light: #1c7ac0;
    --white: #ffffff;
    --ink-grey: #555555;
    --rule-grey: #a8a8a8;
    --band-grey-light: #e2e2e4;
    --band-grey-dark: #6e6f74;
  }
  * { margin: 0; padding: 0; box-sizing: border-box; }
  html, body {
    width: 1200px; height: 800px; overflow: hidden;
    background: var(--bg);
    font-family: "Open Sans", sans-serif;
  }
  .canvas { position: relative; width: 1200px; height: 800px; }

  .card {
    position: absolute; top: 284px;
    width: 430px; height: 238px; overflow: hidden;
  }

  /* Front */
  .card-front {
    left: 110px;
    background: linear-gradient(100deg, var(--brand-blue-dark) 0%, var(--brand-blue-light) 40%, var(--brand-blue) 60%, var(--brand-blue-dark) 100%);
    display: flex; align-items: center; justify-content: center;
  }
  .front-texture { position: absolute; inset: 0; }
  .wordmark-front {
    position: relative;
    font-weight: 700; font-size: 36px; letter-spacing: 2px;
    color: var(--white); text-transform: uppercase;
  }

  /* Back */
  .card-back { left: 638px; background: var(--white); }
  .wordmark-back {
    position: absolute; left: 32px; top: 100px;
    font-weight: 700; font-size: 27px; letter-spacing: 1px;
    color: var(--brand-blue); text-transform: uppercase;
  }
  .divider {
    position: absolute; left: 224px; top: 76px;
    width: 1px; height: 89px; background: var(--rule-grey);
  }
  .contact-block { position: absolute; left: 245px; top: 76px; }
  .person-name {
    font-weight: 600; font-size: 16.5px; color: var(--brand-blue); line-height: 1.2;
  }
  .person-role {
    font-weight: 600; font-size: 9.5px; letter-spacing: 2.5px;
    color: var(--ink-grey); margin-bottom: 8px;
  }
  .contact-list { list-style: none; }
  .contact-item {
    display: flex; align-items: center; gap: 9px;
    font-size: 8.5px; font-weight: 600; color: var(--ink-grey);
    height: 17px;
  }
  .contact-icon { width: 12px; height: 12px; flex: none; }
  .band {
    position: absolute; bottom: 0; height: 8px;
  }
  .band-blue {
    left: 0; width: 254px;
    background: linear-gradient(90deg, var(--brand-blue-dark), var(--brand-blue-light) 40%, var(--brand-blue));
  }
  .band-grey {
    left: 258px; right: 0;
    background: linear-gradient(90deg, var(--band-grey-light), var(--band-grey-dark));
  }
</style>
</head>
<body>
<main class="canvas">
  <section class="card card-front">
    <div class="front-texture" role="img" aria-label="Faint repeated brand-name texture across the blue card face"></div>
    <span class="wordmark-front">Torvalle</span>
  </section>

  <section class="card card-back">
    <span class="wordmark-back">Torvalle</span>
    <div class="divider"></div>
    <div class="contact-block">
      <p class="person-name">Martin Ashworth</p>
      <p class="person-role">CEO</p>
      <ul class="contact-list">
        <li class="contact-item">
          <svg class="contact-icon" viewBox="0 0 12 12" fill="none" stroke="#1467aa" stroke-width="1"><rect x="3" y="0.7" width="6" height="10.6" rx="1"/><line x1="5.3" y1="9.6" x2="6.7" y2="9.6"/></svg>
          +44 7431589027
        </li>
        <li class="contact-item">
          <svg class="contact-icon" viewBox="0 0 12 12" fill="none" stroke="#1467aa" stroke-width="1"><path d="M2.2 1.2l2 0.2 1 2.4-1.3 1a6 6 0 0 0 3.3 3.3l1-1.3 2.4 1 0.2 2c-0.2 0.6-0.8 1-1.5 1C5 10.3 1.7 7 1.2 2.7c0-0.7 0.4-1.3 1-1.5z"/></svg>
          0208 5519372
        </li>
        <li class="contact-item">
          <svg class="contact-icon" viewBox="0 0 12 12" fill="none" stroke="#1467aa" stroke-width="1"><rect x="0.7" y="2.5" width="10.6" height="7" /><path d="M0.7 2.5L6 6.6l5.3-4.1M0.7 9.5l4-3.6M11.3 9.5l-4-3.6"/></svg>
          martin@torvalle.co.uk
        </li>
      </ul>
    </div>
    <div class="band band-blue"></div>
    <div class="band band-grey"></div>
  </section>
</main>
</body>
</html>
```